Unmanned Aerial Systems/Drones Postcard Design

Harbor Vane Aerial is a new local business providing photography and videography for various industries; Real Estate, construction, property management, agriculture, legal, property inspections, building survey and more.Harbor Vane Aerial is authorized and approved for commercial operations by the National Airspace Licensing Bureau.Unauthorized operators maybe subject to large fines and even prosecution.Harbor Vane aerial only uses licensed NALB pilots and an additional visual observer for enhanced safety on each project.

Industry/Entity Type

Business

Requirements
Must have
• The NALB logo connected to the statement "Harbor Vane Aerial is authorized and approved for commercial operations by the National Airspace Licensing Bureau"
Nice to have
• The sunset picture should be the focus as it grabs more attention.
Should not have
• Must not be a generic design, I am looking for something with more style

```html
<!DOCTYPE html>
<html lang="en">
<head>
<meta charset="utf-8">
<title>Harbor Vane Aerial Postcard</title>
<link rel="stylesheet" href="https://fonts.googleapis.com/css2?family=Arimo:wght@400;700&display=swap">
<style>
  :root {
    --page: #ffffff;
    --ink: #111111;
    --sun-core: #ffd46a;
    --sun-mid: #f08a1c;
    --sun-deep: #a3360c;
    --dusk: #2a1208;
    --sky-photo: #8fb3cf;
    --city-photo: #b88f6e;
    --fort-photo: #7e8d97;
    --grass-photo: #5f8a3a;
    --drone-dark: #1d1d1d;
    --badge: #c9a23a;
    --caption: #f4f0e8;
    --rule: #222222;
    --stamp-line: #555555;
  }
  * { margin: 0; padding: 0; box-sizing: border-box; }
  html, body { width: 851px; height: 1200px; overflow: hidden; background: var(--page); }
  body { font-family: "Arimo", Arial, sans-serif; color: var(--ink); position: relative; }

  .card-front {
    position: absolute; left: 14px; top: 0; width: 823px; height: 590px; overflow: hidden;
    background:
      radial-gradient(ellipse 300px 200px at 54% 50%, var(--sun-core) 0%, var(--sun-mid) 40%, transparent 80%),
      linear-gradient(180deg, var(--sun-deep) 0%, var(--sun-mid) 45%, var(--sun-deep) 70%, var(--dusk) 100%);
  }
  .sunset-photo { position: absolute; inset: 0; }
  .brand-title {
    position: absolute; left: 70px; top: 118px;
    font-weight: 700; font-size: 58px; line-height: 1.12; letter-spacing: 1px; text-align: center;
    color: var(--ink);
  }
  .photo-aerial-city {
    position: absolute; left: 511px; top: 14px; width: 298px; height: 199px;
    background: linear-gradient(180deg, var(--sky-photo) 0%, var(--sky-photo) 30%, var(--city-photo) 60%, #8a5d44 100%);
    border: 2px solid #fff;
  }
  .photo-fort {
    position: absolute; left: 86px; top: 468px; width: 184px; height: 99px;
    background: linear-gradient(180deg, #9dc2e2 0%, var(--fort-photo) 45%, var(--grass-photo) 85%);
    border: 2px solid #fff;
  }
  .drone-icon { position: absolute; }
  .drone-icon.top-left { left: 10px; top: 10px; width: 90px; height: 55px; }
  .drone-icon.bottom-right { left: 710px; top: 515px; width: 95px; height: 60px; }
  .drone-icon rect, .drone-icon ellipse, .drone-icon line { fill: var(--drone-dark); stroke: var(--drone-dark); }

  .authorization {
    position: absolute; left: 428px; top: 512px; width: 300px;
    display: flex; align-items: center; gap: 12px;
  }
  .authorization .badge {
    flex: none; width: 56px; height: 56px; border-radius: 50%;
    background: var(--badge); border: 3px solid #fff;
  }
  .authorization p { font-size: 9.5px; line-height: 1.25; color: var(--caption); }

  .card-back {
    position: absolute; left: 14px; top: 604px; width: 823px; height: 590px;
    border: 2px solid var(--rule); background: var(--page);
  }
  .back-copy { position: absolute; left: 26px; top: 38px; width: 350px; }
  .back-copy h2 { font-size: 34px; font-weight: 700; margin-bottom: 10px; }
  .back-copy p { font-size: 20.5px; font-weight: 700; line-height: 1.22; margin-bottom: 26px; }
  .back-copy .contact { font-size: 20.5px; font-weight: 700; line-height: 1.35; }
  .divider {
    position: absolute; left: 409px; top: 70px; width: 3px; height: 460px; background: var(--rule);
  }
  .stamp-box {
    position: absolute; left: 647px; top: 32px; width: 148px; height: 134px;
    border: 2px dashed var(--stamp-line);
  }
</style>
</head>
<body>
  <section class="card-front">
    <div class="sunset-photo" role="img" aria-label="Photograph of a camera drone silhouetted against an orange sunset over the water"></div>
    <svg class="drone-icon top-left" viewBox="0 0 90 55" role="img" aria-label="Small drone silhouette">
      <rect x="32" y="22" width="26" height="12" rx="4"/>
      <line x1="10" y1="14" x2="80" y2="14" stroke-width="3"/>
      <line x1="14" y1="14" x2="34" y2="26" stroke-width="3"/>
      <line x1="76" y1="14" x2="56" y2="26" stroke-width="3"/>
      <ellipse cx="12" cy="10" rx="11" ry="2.5"/>
      <ellipse cx="78" cy="10" rx="11" ry="2.5"/>
      <line x1="38" y1="34" x2="34" y2="48" stroke-width="2"/>
      <line x1="52" y1="34" x2="56" y2="48" stroke-width="2"/>
    </svg>
    <h1 class="brand-title">HARBOR VANE<br>AERIAL</h1>
    <div class="photo-aerial-city" role="img" aria-label="Aerial photograph of a coastal town with red roofs and a bay"></div>
    <div class="photo-fort" role="img" aria-label="Photograph of a historic stone fort on a grassy field"></div>
    <div class="authorization">
      <span class="badge"></span>
      <p>Harbor Vane Aerial is authorized and approved for commercial operations by the National Airspace Licensing Bureau. Unauthorized operators can be subject to fines and even prosecution.</p>
    </div>
    <svg class="drone-icon bottom-right" viewBox="0 0 90 55" role="img" aria-label="Small drone silhouette">
      <rect x="32" y="22" width="26" height="12" rx="4"/>
      <line x1="10" y1="14" x2="80" y2="14" stroke-width="3"/>
      <line x1="14" y1="14" x2="34" y2="26" stroke-width="3"/>
      <line x1="76" y1="14" x2="56" y2="26" stroke-width="3"/>
      <ellipse cx="12" cy="10" rx="11" ry="2.5"/>
      <ellipse cx="78" cy="10" rx="11" ry="2.5"/>
      <line x1="38" y1="34" x2="34" y2="48" stroke-width="2"/>
      <line x1="52" y1="34" x2="56" y2="48" stroke-width="2"/>
    </svg>
  </section>

  <section class="card-back">
    <div class="back-copy">
      <h2>Harbor Vane Aerial</h2>
      <p>Harbor Vane Aerial is a new local business providing photography and videography for various industries; Real Estate, construction, property management, agriculture, legal, property inspections, building survey and more.</p>
      <p>Harbor Vane aerial only uses licensed NALB pilots and an additional visual observer for enhanced safety on each project.</p>
      <div class="contact">
        Email: UAS@HarborVaneAerial.net<br>
        Phone Number: 954-555-0199
      </div>
    </div>
    <div class="divider"></div>
    <div class="stamp-box"></div>
  </section>
</body>
</html>
```